Moravel Aesthetic Doctor

I require an elegant, luxurious looking business card for my aesthetic business. I am a doctor and that will set me aside from competitors. I am planning to provide home and spa based treatments to clients with high expectations. I have attached my logo.

```html
<!DOCTYPE html>
<html lang="en">
<head>
<meta charset="utf-8">
<title>Moravel Aesthetic Doctor – Business Card</title>
<link href="https://fonts.googleapis.com/css2?family=Roboto:wght@400;500;700&display=swap" rel="stylesheet">
<style>
  :root {
    --backdrop: #3b3b3d;
    --card-black: #1c1c1e;
    --card-edge: #2a2a2c;
    --silver: #a9adb3;
    --stripe: #9ba4ae;
    --blue-light: #5cb8ec;
    --blue-deep: #2e8ad2;
    --ink-light: #ffffff;
  }
  * { margin: 0; padding: 0; box-sizing: border-box; }
  html, body {
    width: 799px; height: 1200px; overflow: hidden;
    background: var(--backdrop);
    font-family: "Roboto", sans-serif;
  }
  .sheet {
    width: 799px; height: 1200px;
    display: flex; flex-direction: column; align-items: center; justify-content: space-around;
    padding: 60px 0;
  }
  .card {
    position: relative;
    width: 600px; height: 343px;
    border-radius: 4px;
    overflow: hidden;
    background: var(--card-black);
    box-shadow: 0 14px 30px rgba(0,0,0,0.45);
  }
  /* Front */
  .card-front {
    display: flex; align-items: center; justify-content: center;
  }
  .front-mark {
    display: flex; align-items: center; gap: 16px;
    color: var(--silver);
    font-weight: 400;
    font-size: 30px;
    letter-spacing: 4px;
    text-transform: uppercase;
  }
  .front-mark .dot {
    width: 22px; height: 22px; border-radius: 50%;
    background: var(--silver);
  }
  /* Back */
  .card-back .backdrop { position: absolute; inset: 0; }
  .brand {
    position: absolute; left: 38px; top: 125px;
    color: var(--silver);
    font-weight: 400;
    text-transform: uppercase;
    line-height: 1.15;
  }
  .brand .brand-name { font-size: 40px; letter-spacing: 3px; display: block; }
  .brand .brand-role { font-size: 17px; letter-spacing: 2.4px; display: block; }
  .details {
    position: absolute; left: 346px; top: 78px;
    color: var(--ink-light);
  }
  .doctor-name { font-size: 21px; font-weight: 700; }
  .doctor-name .postnominals { font-size: 11px; font-weight: 400; margin-left: 4px; }
  .qualification { font-size: 14px; line-height: 1.2; margin-top: 2px; }
  .contact-list { list-style: none; margin-top: 12px; font-size: 14px; }
  .contact-list li { display: flex; align-items: center; gap: 10px; height: 21px; }
  .contact-list svg { width: 13px; height: 13px; fill: var(--ink-light); flex: none; }
  .follow { display: flex; align-items: center; gap: 6px; font-size: 14px; margin-top: 2px; }
  .follow .social { width: 15px; height: 15px; border-radius: 50%; background: var(--ink-light); }
</style>
</head>
<body>
<main class="sheet">

  <section class="card card-front" aria-label="Business card front">
    <div class="front-mark"><span class="dot"></span>Moravel Aesthetic Doctor</div>
  </section>

  <section class="card card-back" aria-label="Business card back">
    <svg class="backdrop" viewBox="0 0 600 343" preserveAspectRatio="none" aria-hidden="true">
      <defs>
        <linearGradient id="blue-panel" x1="0" y1="0" x2="0" y2="1">
          <stop offset="0" stop-color="#5cb8ec"/>
          <stop offset="1" stop-color="#2e8ad2"/>
        </linearGradient>
      </defs>
      <rect width="600" height="343" fill="#1c1c1e"/>
      <path d="M300 0 C292 170 250 285 150 343 L600 343 L600 0 Z" fill="#9ba4ae"/>
      <path d="M310 0 C302 172 262 288 166 343 L600 343 L600 0 Z" fill="url(#blue-panel)"/>
    </svg>

    <div class="brand">
      <span class="brand-name">Moravel</span>
      <span class="brand-role">Aesthetic Doctor</span>
    </div>

    <div class="details">
      <p class="doctor-name">Dr Elise Varon<span class="postnominals">MRCPCH MD</span></p>
      <p class="qualification">Australasian Diploma<br>of Aesthetic Medicine</p>
      <ul class="contact-list">
        <li>
          <svg viewBox="0 0 24 24"><path d="M6.6 10.8a15 15 0 0 0 6.6 6.6l2.2-2.2a1 1 0 0 1 1-.25 11.4 11.4 0 0 0 3.6.57 1 1 0 0 1 1 1V20a1 1 0 0 1-1 1A17 17 0 0 1 3 4a1 1 0 0 1 1-1h3.5a1 1 0 0 1 1 1c0 1.25.2 2.45.57 3.57a1 1 0 0 1-.25 1z"/></svg>
          0800 555 014
        </li>
        <li>
          <svg viewBox="0 0 24 24"><path d="M2 5h20v14H2z M2 5l10 8 10-8" fill="none" stroke="#fff" stroke-width="2"/></svg>
          elise@moravel.co.nz
        </li>
        <li>
          <svg viewBox="0 0 24 24"><g fill="none" stroke="#fff" stroke-width="2"><circle cx="12" cy="12" r="9"/><path d="M3 12h18M12 3c3 3 3 15 0 18M12 3c-3 3-3 15 0 18"/></g></svg>
          www.moravel.co.nz
        </li>
      </ul>
      <p class="follow">Follow us on: <span class="social"></span><span class="social"></span></p>
    </div>
  </section>

</main>
</body>
</html>
```